Corporate Design - Immobilienverwaltungsgesellschaft
Zielgruppe
An- und Verkauf, Verwaltung und Vermietung von Immobilien
Zielgruppen: Immobilienspekulanten, Wohnungskäufer, Mieter, Vermieter
Aufgabenstellung
Wir suchen ein hochwertiges Design für eine in Gründung befindliche Gesellschaft mit beschränkter Haftung.
Diese wird aus 2 Gesellschaftern, Katrin und Torsten Fellmer bestehen.
Das Hauptziel der Gesellschaft wird der An- und Verkauf von Immobilien bis zu 1. Million Euro je Kaufobjekt sein
Mit dem Nachnamen der Gesellschafter kann auch gespielt werden, beispielsweise bei Abkürzungen. Die Bezeichnung F&F Verwaltungsgesellschaft mbH ist nicht zwingend, lediglich das Kürzel 'mbH' oder auch 'GmbH' ist aufgrund der Rechtsform der Gesellschaft zwingend aufzunehmen.
Diverse Designideen haben wir bereits vorliegen; hierauf kann aufgebaut werden, siehe Uploads
Unter anderem eine Anlehnung an die unter derselben Firmenadresse der Gesellschaft bestehende Rechtsanwaltskanzlei und deren Cooperate Design wäre eine Idee, jedoch keine zwingende Voraussetzung.

```html
<!DOCTYPE html>
<html lang="de">
<head>
<meta charset="utf-8">
<title>F&amp;F Verwaltungsgesellschaft mbH – Geschäftsausstattung</title>
<link href="https://fonts.googleapis.com/css2?family=Oswald:wght@500&family=Michroma&family=Open+Sans:wght@400;700&family=Libre+Baskerville&family=Caveat&display=swap" rel="stylesheet">
<style>
:root{
  --sky:#6ecbf3;
  --slate:#a0b4c0;
  --ink:#555a5e;
  --grey-text:#8a8f93;
  --paper:#ffffff;
  --line-blue:#6ecbf3;
}
*{margin:0;padding:0;box-sizing:border-box}
html,body{width:927px;height:1200px;overflow:hidden;background:var(--paper)}
.board{position:relative;width:927px;height:1200px}
.top-band{position:absolute;left:288px;top:0;width:581px;height:10px;background:var(--slate)}
.sheet{position:absolute;overflow:hidden;box-shadow:6px 8px 14px rgba(0,0,0,.35)}
.card{width:230px;height:128px}
.card--blue{background:var(--sky);left:284px;top:66px}
.card--slate{background:var(--slate);left:549px;top:65px}
.card--white-front{background:var(--paper);left:284px;top:221px}
.card--white-back{background:var(--paper);left:549px;top:220px}

.brand{position:absolute;display:flex;align-items:flex-start;gap:4px;font-family:"Oswald",sans-serif;font-weight:500;text-transform:uppercase;line-height:1.05;letter-spacing:.04em}
.brand__mark{flex:none;background:currentColor}
.brand--sm{font-size:6.5px}
.brand--sm .brand__mark{width:9px;height:9px}
.brand--md{font-size:9px}
.brand--md .brand__mark{width:12px;height:12px}
.brand--lg{font-size:17px}
.brand--lg .brand__mark{width:22px;height:22px}

.role{position:absolute;left:18px;top:50px;font-family:"Oswald",sans-serif;font-weight:500;font-size:4.5px;letter-spacing:.06em;padding-bottom:2px;width:76px;border-bottom:.6px solid currentColor}
.names{position:absolute;left:18px;top:58px;font-family:"Michroma",sans-serif;font-size:5.6px;line-height:1.15}
.names span{display:block}
.names span+span{padding-left:3px}
.contact{position:absolute;font-family:"Open Sans",sans-serif;font-size:3.9px;line-height:1.55}
.card .contact{left:131px;top:86px}

.on-blue{color:#fff}
.on-white{color:var(--sky)}
.contact.on-white{color:#9fb3c0}

.letterhead{left:283px;top:383px;width:299px;height:423px;background:var(--paper);border-bottom:2px solid var(--line-blue)}
.letterhead .headline{position:absolute;left:80px;top:136px;font-family:"Open Sans",sans-serif;font-weight:700;font-size:12px;color:#7b7f83}
.letterhead .body-copy{position:absolute;left:80px;top:166px;width:200px;font-family:"Open Sans",sans-serif;font-size:4.3px;line-height:1.35;color:#7b7f83}
.letterhead .body-copy p{margin-bottom:5.5px}
.letterhead .closing{position:absolute;left:80px;top:296px;font-family:"Libre Baskerville",serif;font-size:8px;color:#8a8f93}
.letterhead .signature{position:absolute;left:97px;top:308px;font-family:"Caveat",cursive;font-size:12px;color:#8a8f93}
.letterhead .contact{left:32px;top:384px;color:#9fb3c0}
.letterhead .register{position:absolute;left:181px;top:404px;font-family:"Open Sans",sans-serif;font-size:3.9px;line-height:1.55;color:#9fb3c0}

.envelope-back{left:472px;top:383px;width:310px;height:137px;background:var(--paper)}
.envelope-back .flap{position:absolute;left:0;top:0;width:310px;height:33px}
.envelope-back .flap-mark{position:absolute;left:148px;top:8px;width:14px;height:14px;background:#fff}
.envelope-front{left:472px;top:534px;width:310px;height:136px;background:var(--paper);border-bottom:2.5px solid var(--line-blue)}
.envelope-front .contact{left:11px;top:97px;color:#9fb3c0}

.logo-solo{position:absolute;left:622px;top:736px;color:var(--ink)}

.hero{position:absolute;left:283px;top:848px;width:497px;height:330px;background:linear-gradient(160deg,#8b9096 0%,#7c8186 45%,#6a6f74 100%)}
.hero .brand{left:140px;top:138px;color:#fff}
</style>
</head>
<body>
<div class="board">
  <div class="top-band"></div>

  <section class="sheet card card--blue">
    <div class="brand brand--sm on-blue" style="left:126px;top:22px"><span class="brand__mark"></span><span>F&amp;F<br>Verwaltungsgesellschaft mbH</span></div>
    <div class="role on-blue">Manager</div>
    <div class="names on-blue"><span>Katrin Fellmer</span><span>Torsten Fellmer</span></div>
    <div class="contact on-blue">Lindenstraße 27 &nbsp;63739 Musterstadt<br>T: &nbsp;0 61 82/5 38 10-0<br>F: &nbsp;0 61 82/5 38 10-11<br>E-mail: &nbsp;info@ff-verwaltung.de<br>Website: &nbsp;www.ff-verwaltung.de</div>
  </section>

  <section class="sheet card card--slate">
    <div class="brand brand--md on-blue" style="left:58px;top:50px"><span class="brand__mark"></span><span>F&amp;F<br>Verwaltungsgesellschaft mbH</span></div>
  </section>

  <section class="sheet card card--white-front">
    <div class="brand brand--sm on-white" style="left:126px;top:22px"><span class="brand__mark"></span><span>F&amp;F<br>Verwaltungsgesellschaft mbH</span></div>
    <div class="role" style="color:#8a9aa5">Manager</div>
    <div class="names on-white"><span>Katrin Fellmer</span><span>Torsten Fellmer</span></div>
    <div class="contact on-white">Lindenstraße 27 &nbsp;63739 Musterstadt<br>T: &nbsp;0 61 82/5 38 10-0<br>F: &nbsp;0 61 82/5 38 10-11<br>E-mail: &nbsp;info@ff-verwaltung.de<br>Website: &nbsp;www.ff-verwaltung.de</div>
  </section>

  <section class="sheet card card--white-back">
    <div class="brand brand--md on-white" style="left:58px;top:50px"><span class="brand__mark"></span><span>F&amp;F<br>Verwaltungsgesellschaft mbH</span></div>
  </section>

  <section class="sheet letterhead">
    <div class="brand brand--sm on-white" style="left:15px;top:30px"><span class="brand__mark"></span><span>F&amp;F<br>Verwaltungsgesellschaft mbH</span></div>
    <h1 class="headline">Headline here</h1>
    <div class="body-copy">
      <p>Lorem ipsum dolor sit amet, menandri urbanitas pro ut, eleifend constituto, causae consetetur qui ex. Qui mollis noluisse est id, ne labore iisque eripuit pro.</p>
      <p>Ei duo vivendum comprehensam. Qui paulo elitr eu, sed causae verear instructior ex, eam oblique mandamus at.</p>
      <p>Ex nam oblique civibus petentium, ex nam eius assum efficiantur has, scripta vulputate et eos. In summo omnes definitionem eos te. Vel id natum officiis accusata, id deserunt salutandi.</p>
      <p>Has cu tota civibus urbanitas. Duo ei iudico accommodare brute est. Cum an debet constituam, te brute essent iriure recusabo. Et nam quis saepe persius, mea nobis recteque cotidieque pro ad. Ad veri exerci pri.</p>
    </div>
    <div class="closing">Geschäftsführers</div>
    <div class="signature">Name</div>
    <div class="contact">Lindenstraße 27 &nbsp;63739 Musterstadt<br>T: &nbsp;0 61 82/5 38 10-0<br>F: &nbsp;0 61 82/5 38 10-11<br>E-mail: &nbsp;info@ff-verwaltung.de<br>Website: &nbsp;www.ff-verwaltung.de</div>
    <div class="register">Eingetragen beim Amtsgericht Musterstadt HRB 4812<br>Steuer-Nr. 210/334/51207</div>
  </section>

  <section class="sheet envelope-back">
    <svg class="flap" viewBox="0 0 310 33" aria-hidden="true"><path d="M0 0H310L300 20Q295 32 280 32H30Q15 32 10 20Z" fill="var(--sky)"/></svg>
    <span class="flap-mark"></span>
  </section>

  <section class="sheet envelope-front">
    <div class="brand brand--sm on-white" style="left:11px;top:28px"><span class="brand__mark"></span><span>F&amp;F<br>Verwaltungsgesellschaft mbH</span></div>
    <div class="contact">Lindenstraße 27 &nbsp;63739 Musterstadt<br>T: &nbsp;0 61 82/5 38 10-0<br>F: &nbsp;0 61 82/5 38 10-11<br>E-mail: &nbsp;info@ff-verwaltung.de<br>Website: &nbsp;www.ff-verwaltung.de</div>
  </section>

  <div class="brand brand--md logo-solo"><span class="brand__mark"></span><span>F&amp;F<br>Verwaltungsgesellschaft mbH</span></div>

  <section class="hero" role="img" aria-label="Foto eines modernen Bürohochhauses mit Glasfassade, grau getönt">
    <div class="brand brand--lg"><span class="brand__mark"></span><span>F&amp;F<br>Verwaltungsgesellschaft mbH</span></div>
  </section>
</div>
</body>
</html>
```